Business Card design for insurance broker in Denver, CO, USA

I need a business card designed using this logo that was just created. We sell life and disability income insurance to US consumers.
Looking for a professionally designed card to make use of the logo and have something to hand to prospects or new business referral sources. The card could be white, gray, black or whatever you would recommend.

Target Market(s)

US Consumers and other financial professionals that I partner with.

Industry/Entity Type

Insurance Broker

Contact Information for Business Card

Owen T. Farrow, CLU, LUTCF (please note that CLU should have a superscript R in a circle for registered trademark)
President
phone (303) 555-0187
email owen@keelbrookcover.example
4620 W. Halvern Rd, Suite 300, Larkmoor Springs, CO 80499
Somewhere fit in a tagline saying "Your resource for life, long term care, and disability insurance" (maybe the back if it doesn't fit on the front, your call)

Font styles to use
Sans Serif

Requirements
Must have
• Must have logo in correct blue and gray colors, my name, address, phone, email. Order and placement determined by the designer.
• I just want something that looks a more professional than what I could have done using the business card designer tool on pixelbazaar.example or QuillPress, or any other do-it-yourself tool
• A regular rectangular business card with square corners is preferred
Nice to have
• I included the logos of 2 organizations I belong to (GKLS and WOBCE). They should be small, but visible on the back only. If it doesn’t look good, this is not a requirement, feel free to drop it.
Should not have
• Do not add any colors not already in the logo, except use of black and whites which are okay. If you use the logo on the back and want to make that in all black, gray or white, that may be okay as well.

```html
<!DOCTYPE html>
<html lang="en">
<head>
<meta charset="utf-8">
<title>Keelbrook Cover – Business Card</title>
<link href="https://fonts.googleapis.com/css2?family=Montserrat:wght@400;500;600&display=swap" rel="stylesheet">
<style>
  :root {
    --stage: #3b3b3d;
    --card: #1f1f20;
    --card-back: #232324;
    --blue: #1f86cc;
    --gray: #b9b9bb;
    --white: #f4f4f4;
    --rule: #8d8d8f;
  }
  * { margin: 0; padding: 0; box-sizing: border-box; }
  html, body { width: 1200px; height: 900px; overflow: hidden; }
  body {
    background: radial-gradient(circle at 50% 40%, #464648, var(--stage) 70%);
    font-family: "Montserrat", sans-serif;
    color: var(--white);
    position: relative;
  }
  .card {
    position: absolute;
    left: 260px;
    width: 680px;
    height: 390px;
    box-shadow: 0 10px 30px rgba(0,0,0,.45);
  }
  .card--back { top: 40px; background: var(--card-back); }
  .card--front { top: 470px; background: var(--card); }

  /* back */
  .brand-mark {
    position: absolute; left: 0; right: 0; top: 110px;
    display: flex; justify-content: center; align-items: center; gap: 14px;
  }
  .brand-mark__dot { width: 22px; height: 22px; border-radius: 50%; background: var(--gray); }
  .brand-mark__name { font-size: 40px; font-weight: 600; color: var(--gray); letter-spacing: 1px; }
  .tagline {
    position: absolute; left: 0; right: 0; bottom: 62px;
    text-align: center; font-size: 15.5px; font-weight: 400; color: var(--white);
  }
  .tagline__accent { color: var(--blue); }

  /* front */
  .front-logo {
    position: absolute; left: 0; right: 0; top: 42px;
    display: flex; justify-content: center; align-items: center; gap: 12px;
  }
  .front-logo__dot { width: 18px; height: 18px; border-radius: 50%; background: var(--blue); }
  .front-logo__name { font-size: 30px; font-weight: 600; color: var(--blue); letter-spacing: .5px; }

  .person {
    position: absolute; right: 380px; top: 150px; text-align: right;
  }
  .person__name { font-size: 23px; font-weight: 600; letter-spacing: .5px; text-transform: uppercase; }
  .person__creds { font-size: 15px; color: var(--blue); margin-top: 4px; }
  .person__creds sup { font-size: 9px; }
  .person__title { font-size: 16px; margin-top: 2px; }

  .divider {
    position: absolute; left: 320px; top: 150px; width: 2px; height: 90px; background: var(--rule);
  }
  .contacts { position: absolute; left: 345px; top: 150px; list-style: none; }
  .contacts li { display: flex; align-items: center; gap: 14px; font-size: 16px; height: 30px; }
  .contacts svg { width: 18px; height: 18px; fill: var(--blue); flex: none; }

  .address {
    position: absolute; left: 110px; top: 290px;
    display: flex; align-items: center; gap: 14px; font-size: 16.5px;
  }
  .address svg { width: 16px; height: 20px; fill: var(--blue); }
</style>
</head>
<body>
  <section class="card card--back">
    <div class="brand-mark">
      <span class="brand-mark__dot"></span>
      <span class="brand-mark__name">KEELBROOK</span>
    </div>
    <p class="tagline">Your resource for LIFE, Long term CARE &amp; DISABILITY <span class="tagline__accent">INSURANCE</span></p>
  </section>

  <section class="card card--front">
    <div class="front-logo">
      <span class="front-logo__dot"></span>
      <span class="front-logo__name">KEELBROOK COVER</span>
    </div>

    <div class="person">
      <p class="person__name">Owen T. Farrow</p>
      <p class="person__creds">CLU<sup>®</sup>, LUTCF</p>
      <p class="person__title">President</p>
    </div>

    <span class="divider"></span>

    <ul class="contacts">
      <li>
        <svg viewBox="0 0 24 24" aria-hidden="true"><path d="M6.6 10.8a15.1 15.1 0 0 0 6.6 6.6l2.2-2.2c.3-.3.7-.4 1-.2 1.1.4 2.3.6 3.6.6.6 0 1 .4 1 1V20c0 .6-.4 1-1 1A17 17 0 0 1 3 4c0-.6.4-1 1-1h3.5c.6 0 1 .4 1 1 0 1.3.2 2.5.6 3.6.1.3 0 .7-.2 1z"/></svg>
        <span>(303) 555-0187</span>
      </li>
      <li>
        <svg viewBox="0 0 24 24" aria-hidden="true"><path d="M2 5h20v14H2z M3 6l9 7 9-7" fill="none" stroke="#1f86cc" stroke-width="2"/><path d="M2 5h20L12 12z"/></svg>
        <span>owen@keelbrookcover.example</span>
      </li>
      <li>
        <svg viewBox="0 0 24 24" aria-hidden="true"><circle cx="12" cy="12" r="10"/><path d="M2 12h20M12 2c3 3 3 17 0 20M12 2c-3 3-3 17 0 20" fill="none" stroke="#1f1f20" stroke-width="1.5"/></svg>
        <span>www.keelbrookcover.example</span>
      </li>
    </ul>

    <p class="address">
      <svg viewBox="0 0 16 20" aria-hidden="true"><path d="M8 0a8 8 0 0 0-8 8c0 6 8 12 8 12s8-6 8-12a8 8 0 0 0-8-8zm0 11a3 3 0 1 1 0-6 3 3 0 0 1 0 6z"/></svg>
      <span>4620 W. Halvern Rd, Suite 300, Larkmoor Springs, CO 80499</span>
    </p>
  </section>
</body>
</html>
```